New Company Business Card design

Looking for a corporate looking business card utilising my new logo design - the logo i would like embossed as one option and flat as another - simplistic but stylish - less is more - we are an import export business launching into the market - i would like a couple of options as main background - Grey or Black

```html
<!DOCTYPE html>
<html lang="en">
<head>
<meta charset="utf-8">
<title>Meridian Trade Partners – Business Card</title>
<link href="https://fonts.googleapis.com/css2?family=Work+Sans:wght@400;500;600&display=swap" rel="stylesheet">
<style>
  :root {
    --page-bg: #d8d2ca;
    --card-bg: #ecebe8;
    --card-edge: #f7f6f4;
    --brand-blue: #1d5f86;
    --text-grey: #4f4f52;
    --icon-blue: #2f6f96;
  }
  * { margin: 0; padding: 0; box-sizing: border-box; }
  html, body {
    width: 1200px;
    height: 1047px;
    overflow: hidden;
    background: var(--page-bg);
    font-family: "Work Sans", Arial, sans-serif;
  }
  .card {
    position: absolute;
    left: 120px;
    top: 262px;
    width: 960px;
    height: 522px;
    background: var(--card-bg);
    border: 1px solid var(--card-edge);
    border-radius: 18px;
    box-shadow: 0 10px 30px rgba(60, 50, 40, 0.12);
  }
  .brand {
    position: absolute;
    right: 42px;
    top: 118px;
    display: flex;
    align-items: center;
    gap: 14px;
  }
  .brand-dot {
    width: 34px;
    height: 34px;
    border-radius: 50%;
    background: var(--brand-blue);
  }
  .brand-name {
    font-size: 31px;
    font-weight: 500;
    color: var(--brand-blue);
    letter-spacing: 0.3px;
  }
  .contact {
    position: absolute;
    right: 42px;
    top: 262px;
    text-align: right;
    color: var(--text-grey);
  }
  .person-name {
    font-size: 33px;
    font-weight: 500;
    color: var(--brand-blue);
    letter-spacing: 0.5px;
    line-height: 38px;
  }
  .person-role {
    font-size: 20px;
    line-height: 28px;
  }
  .address {
    margin-top: 22px;
    font-size: 21px;
    line-height: 33px;
  }
  .lines {
    margin-top: 14px;
    list-style: none;
    font-size: 21px;
    line-height: 28px;
  }
  .lines li {
    display: flex;
    justify-content: flex-end;
    align-items: center;
    gap: 14px;
  }
  .lines svg {
    width: 14px;
    height: 14px;
    fill: none;
    stroke: var(--icon-blue);
    stroke-width: 1.8;
  }
</style>
</head>
<body>
  <div class="card">
    <div class="brand">
      <span class="brand-dot"></span>
      <span class="brand-name">Meridian Trade Partners</span>
    </div>

    <div class="contact">
      <div class="person-name">DANIEL HART</div>
      <div class="person-role">Director</div>

      <div class="address">
        2750 Harbor View Ave<br>
        Oakland, CA 94607-1120
      </div>

      <ul class="lines">
        <li>555-204-7781
          <svg viewBox="0 0 14 14"><path d="M3 1.5 L5.2 1.5 L6 4.5 L4.6 5.6 C5.3 7.3 6.7 8.7 8.4 9.4 L9.5 8 L12.5 8.8 L12.5 11 C12.5 12 11.8 12.6 10.8 12.5 C6 12 2 8 1.5 3.2 C1.4 2.2 2 1.5 3 1.5 Z"/></svg>
        </li>
        <li>hello@meridiantrade.com
          <svg viewBox="0 0 14 14"><rect x="1.5" y="3" width="11" height="8" rx="1"/><path d="M1.5 3.5 L7 7.5 L12.5 3.5"/></svg>
        </li>
        <li>www.meridiantrade.com
          <svg viewBox="0 0 14 14"><circle cx="7" cy="7" r="5.5"/><ellipse cx="7" cy="7" rx="2.4" ry="5.5"/><path d="M1.5 7 H12.5"/></svg>
        </li>
      </ul>
    </div>
  </div>
</body>
</html>
```